Clear Plastic Card Design

I am looking to have a business card designed from my logo icon. I am looking to match the style of a different business card I have attached in the files.
Looking for a card that is plastic, with layers of transparency in the shape of my logo icon (also attached in the files) - not a circle like the other card. The winning design will incorporate the red icon logo on the front and back and include the charity's name, "Light for the Weary Souls" in the same or similar font, as well as an email and phone number. For now, use the email: email@lightfortheweary-mail.org and the phone number 555-382-7194.
We like how the sample business card has transparency, partial and full opacity layers and a matching color scheme. Files will need to be in vector so that our business card printing company can work with it.
UPDATE:
We've some excellent designs in, thank you everyone! I got an early review from the owner, and he requested a minor redirect to find his perfect design. He wants the design to stand out by NOT being a rectangle. Try instead a circle, square, or best yet - something that falls in the outline of the logo icon, either fully or partially. Thank you, everyone!
Light for the Weary Souls text should be incorporated as well as a phone and email.

```html
<!DOCTYPE html>
<html lang="en">
<head>
<meta charset="utf-8">
<title>Light for the Weary Souls – Business Card</title>
<link href="https://fonts.googleapis.com/css2?family=Questrial&family=Arimo:wght@400;700&display=swap" rel="stylesheet">
<style>
  :root {
    --bg: #e8e5e2;
    --frost-1: #f4f3f2;
    --frost-2: #dcdad8;
    --red: #b3121b;
    --red-dark: #8f0a12;
    --red-light: #d4363b;
    --ink-grey: #4a4a4c;
    --white: #ffffff;
  }
  html, body {
    margin: 0;
    width: 1200px;
    height: 900px;
    overflow: hidden;
    background: var(--bg);
  }
  .card {
    position: absolute;
    left: 200px;
    top: 220px;
    width: 800px;
    height: 460px;
    border-radius: 16px;
    overflow: hidden;
    box-shadow: 0 10px 30px rgba(0,0,0,0.12);
  }
  .card-shape {
    position: absolute;
    inset: 0;
  }
  .brand {
    position: absolute;
    left: 58px;
    top: 120px;
  }
  .brand-dot {
    width: 64px;
    height: 64px;
    border-radius: 50%;
    background: var(--red);
    margin: 0 0 18px 150px;
  }
  .brand-name {
    font-family: "Questrial", sans-serif;
    font-size: 29px;
    line-height: 1.2;
    color: var(--ink-grey);
    margin: 0;
    font-weight: 400;
  }
  .contact {
    position: absolute;
    right: 52px;
    top: 262px;
    text-align: right;
    color: var(--white);
    font-family: "Arimo", sans-serif;
  }
  .contact-name {
    font-size: 31px;
    font-weight: 700;
    letter-spacing: 0.5px;
    margin: 0;
  }
  .contact-role {
    font-size: 18px;
    margin: 4px 0 26px;
  }
  .contact-line {
    display: flex;
    justify-content: flex-end;
    align-items: center;
    gap: 10px;
    font-size: 17px;
    height: 27px;
  }
  .contact-line svg {
    width: 15px;
    height: 15px;
    flex: none;
  }
</style>
</head>
<body>
  <div class="card">
    <svg class="card-shape" viewBox="0 0 800 460" width="800" height="460" aria-hidden="true">
      <defs>
        <linearGradient id="frost" x1="0" y1="0" x2="1" y2="1">
          <stop offset="0" stop-color="var(--frost-1)"/>
          <stop offset="0.6" stop-color="#fbfbfb"/>
          <stop offset="1" stop-color="var(--frost-2)"/>
        </linearGradient>
        <linearGradient id="redPanel" x1="0" y1="1" x2="1" y2="0">
          <stop offset="0" stop-color="var(--red-light)"/>
          <stop offset="0.35" stop-color="var(--red)"/>
          <stop offset="1" stop-color="var(--red-dark)"/>
        </linearGradient>
      </defs>
      <rect class="frost-panel" width="800" height="460" fill="url(#frost)"/>
      <path class="red-panel" fill="url(#redPanel)"
        d="M560 0 H800 V460 H240 C270 445 290 425 312 400 L602 92 C630 60 618 14 560 0 Z"/>
    </svg>

    <div class="brand">
      <div class="brand-dot"></div>
      <p class="brand-name">Light for the<br>Weary Souls</p>
    </div>

    <div class="contact">
      <p class="contact-name">DANIEL REYES</p>
      <p class="contact-role">Founder &amp; CEO</p>
      <div class="contact-line">555-382-7194
        <svg viewBox="0 0 16 16"><path fill="#fff" d="M4 1.5 6.2 4 5 5.6c.8 1.9 2.4 3.5 4.4 4.4L11 8.8l2.5 2.2-1.3 2.5C7 13.3 2.7 9 2.5 3.8Z"/></svg>
      </div>
      <div class="contact-line">email@lightfortheweary-mail.org
        <svg viewBox="0 0 16 16"><rect x="2" y="4" width="12" height="8.5" fill="#fff"/><path d="M2 4 8 9 14 4" fill="none" stroke="var(--red)" stroke-width="1.2"/></svg>
      </div>
      <div class="contact-line">lightforthewearysouls.org
        <svg viewBox="0 0 16 16"><circle cx="8" cy="8" r="6.5" fill="#fff"/><path d="M1.5 8h13M8 1.5c-3 3.5-3 9.5 0 13M8 1.5c3 3.5 3 9.5 0 13" fill="none" stroke="var(--red)" stroke-width="1"/></svg>
      </div>
    </div>
  </div>
</body>
</html>
```